Maple Roster Business Card for recruitment company

We are looking for a Business Card Design that incorporates our personal details and our busines name and logo. We are a specialized search consultancy that recruit Property and Construction professionals.
We would like a business card that stands out and is appealing to the Construction and Property industry as well.

Target Market(s)

people in the construction and property industry

Contact Information for Business Card

Business Name and logo

Font styles to use
Serif

Colors
0094D4
00A9DD
6FCCEA
C7EBF8
E9F6FB

Requirements
Must have
• Business name and logo as well as contact details
Should not have
• No photos of us please

```html
<!DOCTYPE html>
<html lang="en">
<head>
<meta charset="utf-8">
<title>Maple Roster Business Card</title>
<link rel="stylesheet" href="https://fonts.googleapis.com/css2?family=Montserrat:wght@400;500&display=swap">
<style>
  :root {
    --teal: #033d52;
    --white: #ffffff;
    --ink: #3b3f42;
    --backdrop: #e6e8ea;
  }
  * { box-sizing: border-box; margin: 0; padding: 0; }
  html, body { width: 1200px; height: 900px; overflow: hidden; }
  body {
    background: var(--backdrop);
    font-family: "Montserrat", sans-serif;
    display: flex;
    flex-direction: column;
    align-items: center;
    justify-content: center;
    gap: 40px;
  }
  .card {
    position: relative;
    width: 620px;
    height: 354px;
    overflow: hidden;
    box-shadow: 0 6px 18px rgba(0,0,0,0.18);
  }
  .card-front {
    background: var(--teal);
    display: flex;
    align-items: center;
    justify-content: center;
  }
  .brand-name {
    font-weight: 400;
    letter-spacing: 1px;
    text-transform: uppercase;
    white-space: nowrap;
  }
  .card-front .brand-name { color: var(--white); font-size: 46px; }
  .card-back { background: var(--white); }
  .card-back .wave { position: absolute; inset: 0; }
  .card-back .brand-name {
    position: absolute; top: 58px; right: 40px;
    color: var(--teal); font-size: 34px;
  }
  .holder { position: absolute; top: 62px; left: 44px; }
  .holder-name {
    color: var(--teal); font-size: 22px; font-weight: 500;
    text-transform: uppercase; letter-spacing: 0.5px;
  }
  .holder-role {
    color: var(--ink); font-size: 12px; text-transform: uppercase;
    letter-spacing: 1px; margin-top: 2px;
  }
  .contact {
    position: absolute; top: 150px; left: 62px;
    color: var(--ink); font-size: 14px; text-transform: uppercase;
    list-style: none; line-height: 1.45;
  }
  .contact li { display: flex; align-items: center; gap: 10px; }
  .contact svg { width: 16px; height: 16px; fill: var(--teal); flex: none; }
  .contact .address { margin-top: 16px; padding-left: 0; display: block; }
  .website {
    position: absolute; right: 40px; bottom: 44px;
    color: var(--white); font-size: 13px; text-transform: uppercase;
    letter-spacing: 0.5px;
  }
</style>
</head>
<body>
  <section class="card card-front">
    <span class="brand-name">Maple Roster</span>
  </section>

  <section class="card card-back">
    <svg class="wave" viewBox="0 0 620 354" preserveAspectRatio="none" aria-hidden="true">
      <path d="M0,296 C190,296 310,262 430,196 C500,158 560,138 620,132 L620,354 L0,354 Z" fill="var(--teal)"/>
      <path d="M0,322 C210,318 340,282 470,200" fill="none" stroke="var(--white)" stroke-width="4" stroke-linecap="round"/>
    </svg>

    <div class="holder">
      <p class="holder-name">Daniel Hart</p>
      <p class="holder-role">Managing Director</p>
    </div>

    <span class="brand-name">Maple Roster</span>

    <ul class="contact">
      <li>
        <svg viewBox="0 0 24 24" aria-hidden="true"><path d="M6.6 10.8a15.1 15.1 0 0 0 6.6 6.6l2.2-2.2a1 1 0 0 1 1-.25 11.4 11.4 0 0 0 3.6.57 1 1 0 0 1 1 1V20a1 1 0 0 1-1 1A17 17 0 0 1 3 4a1 1 0 0 1 1-1h3.5a1 1 0 0 1 1 1c0 1.25.2 2.45.57 3.57a1 1 0 0 1-.25 1z"/></svg>
        044-987 654 321
      </li>
      <li>
        <svg viewBox="0 0 24 24" aria-hidden="true"><path d="M2 5h20v14H2z M3.5 6.5 12 13l8.5-6.5" fill="var(--teal)" stroke="var(--white)" stroke-width="1.2"/></svg>
        info@mapleroster.com
      </li>
      <li class="address">18 Harbour Street<br>Northvale, 30418</li>
    </ul>

    <span class="website">www.mapleroster.com</span>
  </section>
</body>
</html>
```